TEBSIRK HOA Portal Site for Public

Clean up and organize current website; need website to look good and functional; this is a HOA (homeowner association management) website where homeowners can login and pay their bill, general information about a HOA, monthly newsletter page.
Competitors:
https://quillmarsh.example/
https://dorvinpalms.example/
https://www.kelbrookhomes.example/nevada
http://www.tpw-hoa.example/

Target Market(s)

homeowners

Industry/Entity Type

Real Estate

Coding

Coded - Design and coding required

Number of Pages Required

5+ page

Font styles to use
Serif

Colors
0292cd
33a6d7
e667a6
e34297

Requirements
Must have
• login to pay
• services page
• contact us
• order resale package
Nice to have
• page why an HOA would contract us

```html
<!DOCTYPE html>
<html lang="en">
<head>
<meta charset="utf-8">
<title>Tebsirk Association Management</title>
<link href="https://fonts.googleapis.com/css2?family=Open+Sans:wght@400;600;700;800&display=swap" rel="stylesheet">
<style>
:root{
  --blue:#0292cd;
  --blue-light:#33a6d7;
  --pink:#e34297;
  --pink-light:#e667a6;
  --ink:#333;
  --muted:#555;
  --gray-band:#e5e5e5;
  --gray-soft:#eeeeee;
  --footer:#141414;
  --white:#fff;
}
*{box-sizing:border-box;margin:0;padding:0}
html,body{width:1200px;height:4444px;overflow:hidden}
body{position:relative;font-family:"Open Sans",Arial,sans-serif;color:var(--ink);background:var(--white)}
.abs{position:absolute}
.btn{position:absolute;display:flex;align-items:center;justify-content:center;color:var(--white);font-size:13px;text-transform:uppercase;letter-spacing:.2px}
.btn-blue{background:var(--blue-light);box-shadow:0 2px 0 var(--blue)}
.btn-pink{background:var(--pink)}
.section-title{position:absolute;left:0;width:1200px;text-align:center;color:var(--pink);font-weight:700;font-size:32px;text-transform:uppercase;line-height:1.2}
.center-text{position:absolute;text-align:center;color:var(--muted)}
.photo{position:absolute}
.caption{position:absolute;font-size:15px;line-height:22px;color:var(--ink)}

/* header */
.site-header{position:absolute;left:0;top:0;width:1200px;height:143px;background:var(--white)}
.brand{position:absolute;left:143px;top:84px;font-weight:800;font-size:14px;letter-spacing:.2px;color:#222;text-transform:uppercase}
.brand-mark{position:absolute;left:222px;top:22px;width:48px;height:48px;background:#222;border-radius:50%}
.member-login{left:914px;top:28px;width:141px;height:38px;font-size:12px}
.main-nav{position:absolute;top:100px;left:570px;display:flex;gap:31px;font-size:11px;text-transform:uppercase;color:#333}
.main-nav .active{color:var(--blue)}

/* hero */
.hero{left:0;top:143px;width:1200px;height:471px;background:linear-gradient(100deg,#5a5a52 0%,#7c7a70 35%,#3e3f55 70%,#2a2b45 100%)}
.hero-kicker{left:143px;top:310px;color:var(--white);font-size:24px;font-weight:400}
.hero-title{left:143px;top:338px;color:var(--white);font-size:50px;font-weight:800;letter-spacing:.5px}
.hero-cta{left:143px;top:402px;width:121px;height:39px;font-size:12px}
.hero-arrow{position:absolute;top:362px;width:24px;height:32px;background:rgba(0,0,0,.55)}

/* offer */
.offer-band{left:0;top:967px;width:1200px;height:586px;background:var(--gray-band)}

/* articles */
.article-card{position:absolute;top:1683px;width:440px;height:391px;background:var(--gray-soft)}
.article-card .title{position:absolute;left:22px;top:296px;width:380px;font-size:15px;font-weight:600;line-height:24px;color:#333}
.article-card .date{position:absolute;left:22px;top:352px;font-size:12px;font-weight:600;color:var(--pink)}

/* newsletter */
.newsletter{left:0;top:2153px;width:1200px;height:383px;background:linear-gradient(120deg,#2a2a2a 0%,#3a3734 50%,#262626 100%)}
.newsletter-title{position:absolute;left:0;top:2268px;width:1200px;text-align:center;color:var(--white);font-size:31px;font-weight:700;line-height:41px;text-transform:uppercase}
.email-field{position:absolute;left:388px;top:2362px;width:312px;height:46px;background:var(--white);font-size:14px;color:#555;padding:13px 14px}
.subscribe{left:700px;top:2362px;width:110px;height:46px;font-weight:700;font-size:14px}

/* testimonial */
.testimonial-band{left:0;top:3214px;width:1200px;height:443px;background:var(--gray-soft)}
.quote-badge{position:absolute;left:566px;top:3295px;width:68px;height:68px;border-radius:50%;background:var(--pink)}
.dot{position:absolute;top:3566px;width:12px;height:12px;border-radius:50%;background:#999}

/* footer */
.site-footer{left:0;top:3995px;width:1200px;height:449px;background:var(--footer)}
.footer-col h4{position:absolute;top:4203px;color:var(--white);font-size:15px;font-weight:600;text-transform:uppercase}
.footer-small{position:absolute;font-size:10px;line-height:20px;color:#8a8a8a}
.social{position:absolute;top:4236px;width:40px;height:40px;border:1px solid #666;border-radius:50%}
.rule{position:absolute;left:143px;width:912px;height:1px;background:#333}
</style>
</head>
<body>

<header class="site-header">
  <div class="brand-mark"></div>
  <div class="brand">Tebsirk Association Management</div>
  <div class="btn btn-pink member-login">
    <svg width="14" height="12" viewBox="0 0 14 12" style="margin-right:8px"><path d="M0 4h6V1l5 5-5 5V8H0z" fill="#fff"/><path d="M9 0h5v12H9v-2h3V2H9z" fill="#fff"/></svg>Member Login
  </div>
  <nav class="main-nav">
    <span class="active">Home</span><span>About</span><span>Partner With Us</span><span>Elements of Living</span><span>Contact</span>
  </nav>
</header>

<section>
  <div class="photo hero" role="img" aria-label="Smiling young homeowner standing in front of a house window"></div>
  <div class="hero-arrow" style="left:0"><svg width="24" height="32"><path d="M15 8 8 16l7 8" stroke="#fff" stroke-width="2" fill="none"/></svg></div>
  <div class="hero-arrow" style="left:1176px"><svg width="24" height="32"><path d="M9 8l7 8-7 8" stroke="#fff" stroke-width="2" fill="none"/></svg></div>
  <div class="abs hero-kicker">TEBSIRK manages communities throughout</div>
  <div class="abs hero-title">SOUTHERN NEVADA</div>
  <div class="btn btn-blue hero-cta">Login to Pay</div>
</section>

<section class="about">
  <h2 class="section-title" style="top:686px">About Us</h2>
  <p class="center-text" style="left:143px;top:729px;width:914px;font-size:14px;line-height:27px">Fusce sollicitudin lorem et luctus volutpat. Proin placerat dapibus gravida. In tristique tristique nulla eget hendrerit. Maecenas vel tortor accumsan quam varius imperdiet vel eget elit. Aenean facilisis tincidunt lectus, id dictum nisi luctus eget. Vivamus efficitur ex condimentum, malesuada eros eget, feugiat nibh. Sed tellus ex, imperdiet eget gravida sit amet, volutpat eget turpis. In nec ultricies est. Etiam mattis augue vehicula odio posuere, sit amet tempus lectus luctus.</p>
  <div class="btn btn-blue" style="left:548px;top:848px;width:104px;height:38px">Read More</div>
</section>

<section class="offer">
  <div class="abs offer-band"></div>
  <h2 class="section-title" style="top:1039px">What We Offer</h2>
  <div class="photo" style="left:16px;top:1095px;width:376px;height:263px;background:linear-gradient(160deg,#6f6a64,#3f3c3a)" role="img" aria-label="Crowd of residents mingling at a community event"></div>
  <div class="photo" style="left:412px;top:1095px;width:376px;height:263px;background:linear-gradient(160deg,#8a6a4e,#3f4a5a)" role="img" aria-label="Man using a laptop outdoors"></div>
  <div class="photo" style="left:808px;top:1095px;width:376px;height:263px;background:linear-gradient(180deg,#d9824e 0%,#6b5d66 45%,#2d3038 100%)" role="img" aria-label="Tablet on a table at dusk showing round-the-clock service"></div>
  <div class="caption" style="left:16px;top:1370px">Accessible, licensed Association Managers</div>
  <div class="caption" style="left:412px;top:1370px;width:330px">24 hour Web site access: online account information</div>
  <div class="caption" style="left:808px;top:1370px">24 hour emergency service</div>
  <div class="btn btn-blue" style="left:528px;top:1434px;width:144px;height:40px;font-size:12px">View All Services</div>
</section>

<section class="articles">
  <h2 class="section-title" style="top:1625px">Latest Articles</h2>
  <svg class="abs" style="left:48px;top:1810px" width="18" height="26"><path d="M14 3 5 13l9 10" stroke="#555" stroke-width="3" fill="none"/></svg>
  <svg class="abs" style="left:1130px;top:1810px" width="18" height="26"><path d="M4 3l9 10-9 10" stroke="#555" stroke-width="3" fill="none"/></svg>
  <article class="article-card" style="left:143px">
    <div class="photo" style="left:0;top:0;width:440px;height:279px;background:linear-gradient(150deg,#e9e2d6,#c7a57a 60%,#6e7a4c)" role="img" aria-label="Three friends looking at a laptop together"></div>
    <div class="title">Aging Gracefully – The Retirement Industry in South Florida</div>
    <div class="date">8 AUGUST, 2019</div>
  </article>
  <article class="article-card" style="left:615px">
    <div class="photo" style="left:0;top:0;width:440px;height:279px;background:linear-gradient(180deg,#3a8fd8 0%,#9cb8cc 45%,#6c8a5a 75%,#4f8a34 100%)" role="img" aria-label="Row of suburban houses with green lawns"></div>
    <div class="title">Elderly New Yorkers, Here for the Duration</div>
    <div class="date">8 AUGUST, 2019</div>
  </article>
</section>

<section>
  <div class="photo newsletter" role="img" aria-label="Darkened background of a hand passing house keys"></div>
  <h2 class="newsletter-title">Enter your email address for<br>monthly newsletter</h2>
  <div class="email-field">Email Address</div>
  <div class="btn btn-pink subscribe">SUBSCRIBE</div>
</section>

<section class="videos">
  <h2 class="section-title" style="top:2606px">Tebsirk Association Management Videos</h2>
  <p class="center-text" style="left:140px;top:2660px;width:920px;font-size:11px;line-height:21px;color:#444">Every member of our team has a passion for being the best at what we do, and together, we create communities that residents are proud to call home. We deliver tailored services to meet your needs, as well as value-added services and genuinely helpful service that make a difference, every day, for every resident and community we serve.</p>
  <p class="center-text" style="left:0;top:2724px;width:1200px;font-size:11px;color:#444">Check back often and join us for the latest videos for news, insights, updates and inspiration from Tebsirk Association Management.</p>
  <div class="photo" style="left:16px;top:2764px;width:376px;height:262px;background:linear-gradient(160deg,#3c4a32,#1e2420)" role="img" aria-label="Video still of a woman walking in a garden"></div>
  <div class="photo" style="left:412px;top:2764px;width:376px;height:262px;background:linear-gradient(160deg,#3b4454,#171b22)" role="img" aria-label="Video still of two men in conversation"></div>
  <div class="photo" style="left:808px;top:2764px;width:376px;height:262px;background:linear-gradient(160deg,#5a2e1e,#1c1512)" role="img" aria-label="Video still of an executive speaking to camera"></div>
  <svg class="abs" style="left:184px;top:2875px" width="40" height="40"><circle cx="20" cy="20" r="19" fill="#fff"/><path d="M16 12v16l12-8z" fill="#222"/></svg>
  <svg class="abs" style="left:580px;top:2875px" width="40" height="40"><circle cx="20" cy="20" r="19" fill="#fff"/><path d="M16 12v16l12-8z" fill="#222"/></svg>
  <svg class="abs" style="left:976px;top:2875px" width="40" height="40"><circle cx="20" cy="20" r="19" fill="#fff"/><path d="M16 12v16l12-8z" fill="#222"/></svg>
  <div class="caption" style="left:16px;top:3038px;width:360px">Tebsirk Association Management Exceeds Customer Expectations Every Day</div>
  <div class="caption" style="left:412px;top:3038px">Tebsirk Association Management</div>
  <div class="caption" style="left:808px;top:3038px">Tebsirk Association Management</div>
  <div class="btn btn-blue" style="left:528px;top:3103px;width:144px;height:38px;font-size:12px">View All Videos</div>
</section>

<section>
  <div class="abs testimonial-band"></div>
  <div class="quote-badge"><svg width="68" height="68"><path d="M22 40v-6c0-5 3-8 7-9v4c-2 1-3 2-3 4h3v7zm14 0v-6c0-5 3-8 7-9v4c-2 1-3 2-3 4h3v7z" fill="#fff"/></svg></div>
  <p class="center-text" style="left:143px;top:3376px;width:914px;font-size:16px;line-height:30px;color:#444">You don't need any coding experience at all to craft a beautiful website for your clients. All my customers were very impressed with the layout I created using Craftwell and the delivery time for each project. Its simply the Ultimate Tool you can use for a PressKit site.Craftwell is awesome! I used it on all my customers websites and it's looking unique and beautiful on any of them.</p>
  <div class="center-text" style="left:0;top:3513px;width:1200px;font-size:15px;color:#333">— Dana Whitlow, CEO @ Nimbusware</div>
  <div class="dot" style="left:558px;background:var(--blue-light)"></div>
  <div class="dot" style="left:582px"></div>
  <div class="dot" style="left:606px"></div>
  <div class="dot" style="left:630px"></div>
</section>

<section>
  <h2 class="section-title" style="top:3730px;font-size:31px;line-height:39px">Your best choice for HOA management in the<br>Las Vegas Valley.</h2>
  <p class="center-text" style="left:143px;top:3813px;width:914px;font-size:14px;line-height:24px;color:#444">Tebsirk Association Management is always striving to be of service to the city and community we live and work in. Our team is dedicated into protecting and serving our owners and members.</p>
  <div class="btn btn-blue" style="left:548px;top:3876px;width:104px;height:38px;font-weight:700">PAY DUES</div>
</section>

<footer>
  <div class="abs site-footer"></div>
  <div class="center-text" style="left:0;top:4049px;width:1200px;font-size:14px;color:#888;text-transform:uppercase">Want to talk? Want to ask us a question?</div>
  <div class="abs" style="left:0;top:4072px;width:1200px;display:flex;justify-content:center;align-items:center;color:#fff;font-size:32px">
    <svg width="26" height="26" viewBox="0 0 24 24" style="margin-right:6px"><path d="M6.6 10.8a15 15 0 0 0 6.6 6.6l2.2-2.2c.3-.3.7-.4 1-.2 1.1.4 2.3.6 3.6.6.6 0 1 .4 1 1V20c0 .6-.4 1-1 1A17 17 0 0 1 3 4c0-.6.4-1 1-1h3.5c.6 0 1 .4 1 1 0 1.3.2 2.5.6 3.6.1.3 0 .7-.2 1z" fill="#fff"/></svg>702.555.0148 /&nbsp;&nbsp;
    <svg width="28" height="22" viewBox="0 0 28 22" style="margin-right:6px"><rect width="28" height="22" rx="2" fill="#fff"/><path d="M1 2l13 10L27 2" stroke="#141414" stroke-width="2.5" fill="none"/></svg>hello@tebsirk.example
  </div>
  <div class="rule" style="top:4155px"></div>

  <div class="footer-col"><h4 style="left:145px">About Us</h4></div>
  <p class="footer-small" style="left:145px;top:4232px;width:270px">As the leading residential property management company in North America, we work hard to help your community thrive. Our dedication, responsiveness and integrity are why thousands of communities across the U.S. and Canada</p>

  <div class="footer-col"><h4 style="left:496px">About</h4></div>
  <p class="footer-small" style="left:496px;top:4230px">Home<br>About<br>Partner With Us<br>Elements Of living<br>Contact Us</p>

  <div class="footer-col"><h4 style="left:664px">Get In Touch</h4></div>
  <p class="footer-small" style="left:664px;top:4230px">4120 S Marlow Ave Henderson, NV 89000<br>Phone:(702) 555-0148<br>Email: hello@tebsirk.example</p>

  <div class="footer-col"><h4 style="left:917px">Follow Us On</h4></div>
  <div class="social" style="left:918px"></div>
  <div class="social" style="left:966px"></div>
  <div class="social" style="left:1014px"></div>

  <div class="rule" style="top:4372px"></div>
  <div class="center-text" style="left:0;top:4399px;width:1200px;font-size:10px;color:#8a8a8a">Copyright © 2019 Tebsirk HOA. All rights reserved.</div>
</footer>

</body>
</html>
```